Advertising company unique advertising platform

we need a logo design for a new company based in Australia Melbourne. We develop innovated advertising platform where consumer can use this platform to get regular discount, as business owner they can use this platform for free advertisement. Payment for this advertisement platform only payable every two weeks, when I generate revenue for their business

Industry/Entity Type

Advertising

Contact Information for Business Card

Dale Morven | Co-Founder |Managing Director
Suite 718 240 Wattlebrook Lane Melbourne Vic 3000

ABN 38 614 207 923
Tel: +61 0487 259 318 | Email: dale.morven@plivorantu.com

Font styles to use
Decorative
Script

Requirements
Must have
• Try few different design and some round corner business card
Should not have
• One round corner business card...try 4 different colour background not only black, make sure two side is designed. Be creative so imagine you are giving this to a client make sure has wow factor, if you can also try one design with engrave like all the logo, words look 3d feel
• The word Advertising Platform use attached file font

```html
<!DOCTYPE html>
<html lang="en">
<head>
<meta charset="utf-8">
<title>Kelvara Loop — Business Card</title>
<link href="https://fonts.googleapis.com/css2?family=Roboto:wght@400;500;700&display=swap" rel="stylesheet">
<style>
  :root {
    --page: #e9e6e2;
    --card-dark: #262626;
    --card-back: #2a2521;
    --pattern-brown: #4a2f22;
    --pattern-teal: #1f4f4a;
    --accent-red: #f0412a;
    --accent-orange: #f58a2e;
    --accent-yellow: #f7c33a;
    --accent-teal: #1fe0b4;
    --accent-blue: #4aa6f0;
    --text-light: #ffffff;
    --text-dark: #3a2a1e;
    --divider: #8a8a8a;
  }
  * { box-sizing: border-box; margin: 0; padding: 0; }
  html, body { width: 1200px; height: 886px; overflow: hidden; }
  body {
    background: var(--page);
    font-family: "Roboto", Arial, sans-serif;
    position: relative;
  }
  .card {
    position: absolute;
    width: 560px;
    height: 320px;
    border-radius: 26px;
    overflow: hidden;
    box-shadow: 0 14px 30px rgba(0,0,0,0.25);
  }
  /* Back side */
  .card-back { left: 50px; top: 100px; background: var(--card-back); }
  .card-back .pattern-fill {
    position: absolute; inset: 0;
    background: radial-gradient(circle at 30% 40%, var(--pattern-brown), transparent 60%),
                radial-gradient(circle at 75% 65%, var(--pattern-teal), transparent 55%),
                var(--card-back);
    opacity: 0.8;
  }
  .card-back .brand-block {
    position: absolute; left: 0; right: 0; top: 112px;
    text-align: center;
  }
  .brand-name {
    font-weight: 700;
    color: var(--accent-orange);
    font-size: 50px;
    letter-spacing: 1px;
    line-height: 1;
  }
  .website {
    margin-top: 16px;
    color: var(--text-light);
    font-size: 15px;
    letter-spacing: 4px;
  }
  /* Front side */
  .card-front { left: 590px; top: 460px; background: var(--card-dark); }
  .logo-area {
    position: absolute; left: 36px; top: 84px; width: 230px;
    display: flex; align-items: center; gap: 12px;
  }
  .logo-dot {
    width: 34px; height: 34px; border-radius: 50%;
    background: var(--accent-orange); flex: none;
  }
  .logo-area .brand-name { font-size: 30px; }
  .divider {
    position: absolute; left: 282px; top: 52px;
    width: 1px; height: 150px; background: var(--divider);
  }
  .contact {
    position: absolute; left: 304px; top: 58px;
  }
  .person-name {
    color: var(--accent-red); font-weight: 500; font-size: 22px;
    text-transform: uppercase; line-height: 1.1;
  }
  .person-role {
    color: var(--accent-teal); font-weight: 500; font-size: 16px;
    text-transform: uppercase; line-height: 1.2; margin-top: 4px;
  }
  .contact-list { list-style: none; margin-top: 12px; }
  .contact-list li {
    display: flex; align-items: center; gap: 10px;
    color: var(--text-light); font-size: 15.5px; line-height: 1.5;
  }
  .contact-list svg { width: 13px; height: 13px; flex: none; }
  .footer-band {
    position: absolute; left: 0; right: 0; bottom: 0; height: 92px;
    background: linear-gradient(90deg, var(--accent-red) 0%, var(--accent-orange) 25%, var(--accent-yellow) 55%, var(--accent-orange) 80%, var(--accent-teal) 90%, var(--accent-blue) 100%);
  }
  .company-details {
    position: absolute; left: 40px; top: 22px;
    color: var(--text-dark); font-size: 15.5px; line-height: 1.45;
  }
  .band-dot {
    position: absolute; right: 54px; top: 24px;
    width: 42px; height: 42px; border-radius: 50%;
    background: var(--accent-red);
  }
</style>
</head>
<body>
  <section class="card card-back" aria-label="Card back">
    <div class="pattern-fill" role="img" aria-label="Repeating brand symbol pattern in dark brown and teal"></div>
    <div class="brand-block">
      <div class="brand-name">Kelvara Loop</div>
      <div class="website">www.plivorantu.com</div>
    </div>
  </section>

  <section class="card card-front" aria-label="Card front">
    <div class="logo-area">
      <span class="logo-dot"></span>
      <span class="brand-name">Kelvara Loop</span>
    </div>
    <div class="divider"></div>
    <div class="contact">
      <div class="person-name">Dale Morven</div>
      <div class="person-role">Co-Founder<br>Managing Director</div>
      <ul class="contact-list">
        <li>
          <svg viewBox="0 0 24 24" aria-hidden="true"><path fill="#f0412a" d="M6.6 10.8a15.1 15.1 0 0 0 6.6 6.6l2.2-2.2a1 1 0 0 1 1-.25 11.4 11.4 0 0 0 3.6.57 1 1 0 0 1 1 1V20a1 1 0 0 1-1 1A17 17 0 0 1 3 4a1 1 0 0 1 1-1h3.5a1 1 0 0 1 1 1c0 1.25.2 2.45.57 3.57a1 1 0 0 1-.25 1z"/></svg>
          +61 0487 259 318
        </li>
        <li>
          <svg viewBox="0 0 24 24" aria-hidden="true"><path fill="#f0412a" d="M2 5h20v14H2z"/><path fill="none" stroke="#262626" stroke-width="2" d="M2 5l10 8 10-8"/></svg>
          dale.morven@plivorantu.com
        </li>
      </ul>
    </div>
    <div class="footer-band">
      <div class="company-details">
        Plivorantu | ABN 38 614 207 923<br>
        Suite 718 240 Wattlebrook Lane, Melbourne Vic 3000
      </div>
      <span class="band-dot"></span>
    </div>
  </section>
</body>
</html>
```